New Business Card Design for Manufacturing

We are an engineering/manufacturing company that offers Advanced machining/assembly/engineering services, as well as innovative products for the heavy duty engine cooling markets.

We are looking to get a new business card designed that is clean and modern looking, but still fits the wide range of technical/skilled work we do.

- We hope to use this design as the base for other design work in new Presentations, web, and print work.

Industry/Entity Type

Engineering

Contact Information for Business Card

Our preferred color of blue is (RGB) 22/71/159 but can vary slightly from that color. Our content will be our Logo and full company name (Vantrell Forge Works, Inc.), company address, name, job title, phone number with extension, cell number, fax number, website, and email address on the cards.
We'd like the full company name next to the logo, but we are open to other interpretations of that layout.
Preferably, we would like the back side to be clean with just our logo, and the front to contain all of the contact information.

Colors
2f74b4
0355a3
85abd2

Requirements
Must have
• - Logo, company name, needed content - We are open to interpretation beyond that.
• - Standard size business card.
• - Horizontal orientation.
• - Enough space for lengthy names / job titles (for example, a job title could read "Directory of Human Resources" or "V.P. of Governmental Affairs"). We need this to look clean, whether the title be short (CEO) or long (as described above).

```html
<!DOCTYPE html>
<html lang="en">
<head>
<meta charset="utf-8">
<title>Vantrell Forge Works – Business Card</title>
<link rel="stylesheet" href="https://fonts.googleapis.com/css2?family=Open+Sans:wght@400;600;800&display=swap">
<style>
  :root {
    --backdrop: #4a4a4a;
    --card: #1d1d1f;
    --card-edge: #111113;
    --gloss: #2c2c2f;
    --brand-blue: #1a66c2;
    --text-light: #f2f2f2;
    --text-muted: #cfcfcf;
  }
  * { margin: 0; padding: 0; box-sizing: border-box; }
  html, body {
    width: 799px; height: 1200px; overflow: hidden;
    background: var(--backdrop);
    font-family: "Open Sans", Arial, sans-serif;
  }
  .canvas {
    position: relative; width: 799px; height: 1200px;
    display: flex; flex-direction: column; align-items: center; justify-content: space-around;
    padding: 60px 0;
  }
  .card {
    position: relative; width: 640px; height: 366px;
    background: var(--card);
    border: 1px solid var(--card-edge);
    box-shadow: 0 18px 40px rgba(0,0,0,.45);
  }
  /* Logo side */
  .card--logo { display: flex; align-items: center; justify-content: center; }
  .wordmark {
    font-weight: 800; font-size: 86px; letter-spacing: 2px;
    color: var(--gloss);
  }
  /* Contact side */
  .card--contact { padding: 34px 40px; }
  .person-name { color: var(--brand-blue); font-size: 25px; font-weight: 600; line-height: 1.15; }
  .person-title { color: var(--text-light); font-size: 14px; margin-bottom: 22px; }
  .company-name { color: var(--brand-blue); font-size: 16px; font-weight: 600; margin-bottom: 6px; }
  .contact-list { list-style: none; color: var(--text-light); font-size: 16px; line-height: 1.42; }
  .contact-list li { display: flex; align-items: center; gap: 10px; }
  .contact-list svg { width: 13px; height: 13px; fill: var(--brand-blue); flex: none; }
  .contact-list .address { padding-left: 0; }
  .card--contact .wordmark {
    position: absolute; right: 36px; bottom: 34px;
    font-size: 50px; color: var(--brand-blue);
  }
</style>
</head>
<body>
<main class="canvas">
  <section class="card card--logo" aria-label="Card back">
    <span class="wordmark">VANTRELL</span>
  </section>

  <section class="card card--contact" aria-label="Card front">
    <h1 class="person-name">Marcus Ellery Hale</h1>
    <p class="person-title">Managing Director</p>
    <p class="company-name">Vantrell Forge Works, Inc.</p>
    <ul class="contact-list">
      <li><svg viewBox="0 0 16 16"><path d="M3 1h3l1.5 4-2 1.2a9 9 0 0 0 4.3 4.3L11 8.5l4 1.5v3a2 2 0 0 1-2 2A13 13 0 0 1 1 3a2 2 0 0 1 2-2z"/></svg>555-0142-2210 (VFW)</li>
      <li><svg viewBox="0 0 16 16"><rect x="4" y="0.5" width="8" height="15" rx="1.5"/></svg>555-0187-3364</li>
      <li><svg viewBox="0 0 16 16"><path d="M4 1h8v4H4zM1 6h14v6h-3v3H4v-3H1z"/></svg>555-0199-4471</li>
      <li><svg viewBox="0 0 16 16"><circle cx="8" cy="8" r="7"/></svg>www.vantrellforge.example</li>
      <li><svg viewBox="0 0 16 16"><path d="M1 3h14v10H1zM1 3l7 6 7-6"/></svg>mhale@vantrellforge.example</li>
      <li class="address">78 Ridgeline Ave., Harlow City,</li>
      <li class="address">Brookfield, US 40521</li>
    </ul>
    <span class="wordmark">VANTRELL</span>
  </section>
</main>
</body>
</html>
```